Life Coaching and Personal Development Business. Needs Business Card with Logo

We are a Life Coaching and Personal Development Business based in Melbourne, Victoria. We specialise in assisting Individuals who find themselves at cross roads due to career, relationships or just life experiences that are preventing them from having extraordinary lives in happiness, finance or relationships or just being disconnected from a sense of purpose. Our motto is "we help you get there".

Reason: I am awaiting final concepts from a couple of designers

Reason: Deadline passed so now would like to see more options.

Target Market(s)

Individuals who want to move through the cross roads and who are aware that they require help to do so. They are seeking happy, for filing lives through all aspects career, relationships, family and finance

Industry/Entity Type

Finance

Font styles to use
Script

Requirements
Must have
• logo which is representative of moving forward
Business Name: RD Maple Harbour
ABN: 5038617294

I do not have a preference with colour but I do not want red orange or green

Should not have
• The card must not be to busy.

```html
<!DOCTYPE html>
<html lang="en">
<head>
<meta charset="UTF-8">
<title>RD Maple Harbour – Business Card</title>
<link rel="stylesheet" href="https://fonts.googleapis.com/css2?family=Tinos:ital,wght@0,400;1,400&display=swap">
<style>
  :root {
    --harbour: #3aa6c9;
    --harbour-deep: #1d87ab;
    --ink: #111111;
    --paper: #ffffff;
    --edge: #e6e6e6;
    --serif: "Tinos", "Times New Roman", serif;
  }
  html, body {
    margin: 0;
    padding: 0;
    overflow: hidden;
    background: var(--paper);
  }
  .canvas {
    position: relative;
    width: 884px;
    height: 1200px;
    overflow: hidden;
    background: var(--paper);
    font-family: var(--serif);
    color: var(--ink);
  }
  /* Front face */
  .card-front {
    position: absolute;
    left: 0;
    top: 0;
    width: 882px;
    height: 568px;
    border: 1px solid var(--edge);
    background: var(--paper);
  }
  .contact-person {
    position: absolute;
    left: 655px;
    top: 22px;
  }
  .person-name {
    font-size: 26px;
    line-height: 1;
    margin: 0 0 12px;
  }
  .person-phone {
    display: flex;
    align-items: center;
    gap: 10px;
    font-size: 26px;
    line-height: 1;
  }
  .person-phone svg { width: 14px; height: 26px; }
  .brand {
    position: absolute;
    left: 208px;
    top: 243px;
    height: 114px;
    display: flex;
    align-items: center;
  }
  .brand-mark {
    width: 96px;
    height: 96px;
    border-radius: 50%;
    background: var(--harbour-deep);
  }
  .brand-divider {
    width: 1px;
    height: 114px;
    background: var(--ink);
    margin: 0 28px 0 33px;
  }
  .brand-name {
    font-size: 31px;
    color: var(--harbour-deep);
    line-height: 1;
    margin: 0 0 12px;
    font-weight: 400;
  }
  .brand-abn {
    font-size: 20px;
    line-height: 1;
  }
  /* Back face */
  .card-back {
    position: absolute;
    left: 0;
    top: 632px;
    width: 884px;
    height: 568px;
    background: var(--harbour);
  }
  .motto {
    position: absolute;
    left: 0;
    right: 0;
    top: 244px;
    text-align: center;
    font-style: italic;
    font-size: 69px;
    line-height: 1;
    margin: 0;
    font-weight: 400;
  }
  .back-contact {
    position: absolute;
    left: 0;
    right: 0;
    top: 490px;
    text-align: center;
    font-size: 20px;
    line-height: 28px;
  }
  .back-contact p {
    margin: 0;
    display: flex;
    justify-content: center;
    align-items: center;
    gap: 8px;
  }
  .back-contact svg { width: 18px; height: 18px; }
</style>
</head>
<body>
<main class="canvas">
  <section class="card-front">
    <div class="contact-person">
      <p class="person-name">Claire Lindqvist</p>
      <div class="person-phone">
        <svg viewBox="0 0 14 26" aria-hidden="true">
          <rect x="1" y="1" width="12" height="24" rx="2" fill="none" stroke="#1d87ab" stroke-width="2"/>
          <line x1="3" y1="20" x2="11" y2="20" stroke="#1d87ab" stroke-width="1.5"/>
        </svg>
        <span>04153 28861</span>
      </div>
    </div>
    <div class="brand">
      <div class="brand-mark" aria-hidden="true"></div>
      <div class="brand-divider"></div>
      <div class="brand-text">
        <h1 class="brand-name">RD Maple Harbour</h1>
        <div class="brand-abn">ABN: 5038617294</div>
      </div>
    </div>
  </section>

  <section class="card-back">
    <h2 class="motto">"We help you get there"</h2>
    <div class="back-contact">
      <p>
        <svg viewBox="0 0 18 18" aria-hidden="true">
          <rect x="1" y="4" width="16" height="11" fill="none" stroke="#111" stroke-width="1.3"/>
          <polyline points="1,4 9,11 17,4" fill="none" stroke="#111" stroke-width="1.3"/>
          <line x1="1" y1="15" x2="7" y2="9" stroke="#111" stroke-width="1.1"/>
          <line x1="17" y1="15" x2="11" y2="9" stroke="#111" stroke-width="1.1"/>
        </svg>
        <span>claire@rdmapleharbour.com.au</span>
      </p>
      <p>
        <svg viewBox="0 0 18 18" aria-hidden="true">
          <path d="M9 1 C5 1 3 4 3 7 C3 11 9 17 9 17 C9 17 15 11 15 7 C15 4 13 1 9 1 Z" fill="#111"/>
          <circle cx="9" cy="7" r="2.3" fill="#3aa6c9"/>
        </svg>
        <span>P.O. Box 4127, Sandringham VIC 3191</span>
      </p>
    </div>
  </section>
</main>
</body>
</html>
```